Single-sided business card for restaurant velmora with new logo made on this site

Business card options with new logo including restaurant name, address, phone number and website. This business card is single-sided only and will be presented at the hostess desk for clients to take. I would like to see options based on a cream card background, a white card background, a yellow card background and a burgundy colored background. It needs to be elegant and traditional.

Target Market(s)

local and international crowd

Industry/Entity Type

restaurant

Contact Information for Business Card

address, website and phone number

Font styles to use
Serif

Colors
EE7325
F08F49
F5BC92
FAE3D3
FDF4ED

Requirements
Must have
• new logo, address, phone number, website
Should not have
• more than three colors

```html
<!DOCTYPE html>
<html lang="es">
<head>
<meta charset="utf-8">
<title>Velmora — tarjetas de presentación</title>
<link href="https://fonts.googleapis.com/css2?family=Cinzel:wght@400;500&display=swap" rel="stylesheet">
<style>
  :root {
    --backdrop: #d9d2c7;
    --card: #fafafa;
    --amber: #efae2f;
    --ink: #2f1a14;
    --brand: #3a1d15;
  }
  * { margin: 0; padding: 0; box-sizing: border-box; }
  html, body { width: 900px; height: 1200px; overflow: hidden; }
  body {
    background: var(--backdrop);
    position: relative;
    font-family: "Cinzel", Georgia, serif;
    color: var(--ink);
  }
  .card {
    position: absolute;
    background: var(--card);
    box-shadow: 0 2px 6px rgba(0,0,0,0.18);
  }
  .card--plain { left: 73px; top: 130px; width: 777px; height: 452px; }
  .card--framed { left: 70px; top: 615px; width: 785px; height: 465px; }
  .card__frame {
    position: absolute;
    left: 27px; top: 28px; right: 25px; bottom: 28px;
    border: 2px solid var(--amber);
  }
  .brand {
    position: absolute;
    width: 230px;
    text-align: center;
  }
  .card--plain .brand { left: 77px; top: 128px; }
  .card--framed .brand { left: 80px; top: 133px; }
  .brand__square {
    display: block;
    width: 112px; height: 112px;
    margin: 0 auto;
    background: var(--amber);
  }
  .brand__name {
    display: block;
    margin-top: 20px;
    font-size: 34px;
    font-weight: 500;
    letter-spacing: 4px;
    color: var(--brand);
    line-height: 1;
  }
  .divider {
    position: absolute;
    width: 2px;
    background: var(--amber);
  }
  .card--plain .divider { left: 367px; top: 92px; height: 268px; }
  .card--framed .divider { left: 371px; top: 95px; height: 275px; }
  .contact {
    position: absolute;
    font-size: 22px;
    font-weight: 500;
    line-height: 31.5px;
    letter-spacing: 0.3px;
    font-style: normal;
    white-space: nowrap;
  }
  .card--plain .contact { left: 427px; top: 92px; }
  .card--framed .contact { left: 433px; top: 94px; }
  .contact__rule {
    width: 92px; height: 2px;
    background: var(--amber);
    margin: 24px 0 21px;
  }
</style>
</head>
<body>

  <section class="card card--plain" aria-label="Tarjeta de presentación, fondo blanco">
    <div class="brand">
      <span class="brand__square"></span>
      <span class="brand__name">VELMORA</span>
    </div>
    <div class="divider"></div>
    <address class="contact">
      <p>Restaurant Velmora</p>
      <p>Jazmín 418</p>
      <p>Bahía de Solmira,</p>
      <p>Costa Alta CP 40981</p>
      <div class="contact__rule"></div>
      <p>Reservaciones</p>
      <p>321-555-0142</p>
      <p>www.velmora.com.mx</p>
    </address>
  </section>

  <section class="card card--framed" aria-label="Tarjeta de presentación con marco">
    <div class="card__frame"></div>
    <div class="brand">
      <span class="brand__square"></span>
      <span class="brand__name">VELMORA</span>
    </div>
    <div class="divider"></div>
    <address class="contact">
      <p>Restaurant Velmora</p>
      <p>Jazmín 418</p>
      <p>Bahía de Solmira,</p>
      <p>Costa Alta CP 40981</p>
      <div class="contact__rule"></div>
      <p>Reservaciones</p>
      <p>321-555-0142</p>
      <p>www.velmora.com.mx</p>
    </address>
  </section>

</body>
</html>
```